International Petrochemical business needs a web design for Clearway Desk system

We need a web design for a "Clearway Desk" system for an international petrochemical company. The web site is used internally within the company. It is hosted by an internal department which provides government permit request service for other departments.

We would like to see designs of two pages using color light blue. (home page, internal page as attached).
Home Page:
1. Header has a background image and small animation. Header on home page can be taller than the header of the internal page.
2. Layout as attached.

Internal Page:
1. Header can use the same background image as the home page and can be shorter to utilize the page for content.
2. The blue icon behind every captions represent an icon. When user move mouse over this icon, it displays the caption in Thai language as a tooltip. This icon needs to be redesign.

The final design should communicate the followings:
- Excellent service provided system in terms of time and accurary
- Rapid growth of business via building petrochemical refinery plant
Updates

For Internal Page, the blue circle behind every captions represent an icon. When mouse over this icon, a tool tip showing the caption in Thai language is shown. Please also design this icon..

There are more feedbacks from customer as followed:

1. Banner should consists of 
    1.1 "Approved" stamp on paper
    1.2 An image of Garuda. It is used on every government documents in Thailand
    1.3 Image of petrochemical plant
2. Each menu item (Home, Permit, Search, etc) should have different colors. Drop down menu will use the same color as its parent menu item.
3. Overall tone of the web page should be light blue with background of the body the web page in white
4. "New Request" button should use green color with icon on it
5. Table header of each box in the body of the page should use dark blue background with text in white

Please kindly submit your revisions.
Thank you.

Industry/Entity Type

Business

Requirements
Must have
• 1. Design for 1024x768 screen resolution
2. Use light blue theme
3. Background of header where the company logo is must have white background

```html
<!DOCTYPE html>
<html lang="en">
<head>
<meta charset="utf-8">
<title>Clearway Desk – Home</title>
<link href="https://fonts.googleapis.com/css2?family=Open+Sans:wght@400;600;700&family=Sarabun:wght@400&display=swap" rel="stylesheet">
<style>
  :root{
    --sky:#00aeef;
    --sky-deep:#0a8fc4;
    --accent:#12a3e3;
    --ink:#333333;
    --ink-soft:#555555;
    --head:#2b2b2b;
    --rule:#d9d9d9;
    --link:#0645ad;
    --tab:#ececec;
    --tab-active:#2e2e2e;
    --page:#ffffff;
    --green-top:#a6dd4f;
    --green-bot:#6cb520;
    --pager-dark:#3f5674;
  }
  *{box-sizing:border-box;margin:0;padding:0}
  html,body{width:1200px;height:1121px;overflow:hidden}
  body{
    font-family:"Open Sans",Arial,sans-serif;
    color:var(--ink);
    background:linear-gradient(180deg,#0b86b8 0,var(--sky) 90px,var(--sky) 100%);
    position:relative;
  }
  .page{position:absolute;left:95px;top:13px;width:1011px;height:1063px;background:var(--page)}
  .masthead{position:absolute;left:0;top:0;width:1011px;height:131px;background:linear-gradient(180deg,#ffffff 0,#f4f4f4 100%)}
  .masthead-bar{position:absolute;left:0;top:0}
  .system-name{position:absolute;right:32px;top:5px;color:#fff;font-size:22px;font-weight:400;letter-spacing:.2px}
  .brand{position:absolute;left:53px;top:34px;display:flex;align-items:center;gap:8px}
  .brand-dot{width:22px;height:22px;border-radius:50%;background:var(--accent)}
  .brand-name{color:var(--accent);font-weight:700;font-size:14px;line-height:1}
  .nav{position:absolute;left:22px;top:91px;height:40px;display:flex}
  .nav a{position:relative;display:block;width:128px;height:40px;margin-right:-10px;text-align:center;line-height:42px;
    font-size:14.5px;font-weight:700;color:var(--ink);text-decoration:none;text-transform:uppercase}
  .nav a svg{position:absolute;left:0;top:0;z-index:0}
  .nav a span{position:relative;z-index:1}
  .nav a.is-active{color:#fff;width:150px;z-index:5}
  .search{position:absolute;left:773px;top:89px;width:213px;height:28px;border:1px solid #cfcfcf;border-radius:14px;background:#fff;box-shadow:inset 0 1px 2px rgba(0,0,0,.12)}
  .search-btn{position:absolute;right:-1px;top:-1px;width:40px;height:28px;border-radius:14px;background:#2a2a2a;display:flex;align-items:center;justify-content:center}
  .hero{position:absolute;left:0;top:131px;width:1011px;height:214px;
    background:linear-gradient(180deg,#6a4f8c 0,#8a6aa8 25%,#3c3f52 60%,#2a3028 100%)}
  .hero-caption{position:absolute;left:0;bottom:0;width:100%;height:33px;background:rgba(0,0,0,.62);color:#fff;font-size:14.5px;line-height:33px;padding-left:28px}
  .hero-dots{position:absolute;right:38px;top:11px;display:flex;gap:4px}
  .hero-dots i{width:12px;height:12px;border-radius:50%;background:#fff}
  .hero-dots i.on{background:var(--accent)}
  .body-shade{position:absolute;left:0;top:345px;width:1011px;height:60px;background:linear-gradient(180deg,#e6e6e6,#ffffff)}
  .panel{position:absolute}
  .panel-title{font-size:24.5px;font-weight:700;color:var(--head);line-height:1;height:34px}
  .panel-title em{font-style:normal;color:var(--accent)}
  .grid{border-collapse:collapse;table-layout:fixed;width:100%;font-size:13.5px}
  .grid th{background:var(--head);color:#fff;font-weight:600;text-align:left;height:32px;padding:0 7px;border-left:1px solid #fff;font-size:13.5px}
  .grid th:first-child{border-left:0}
  .grid td{height:31.5px;padding:0 7px;border-bottom:1px solid var(--rule);color:var(--ink-soft)}
  .grid td a{color:var(--link)}
  .grid .num{text-align:right;padding-right:26px}
  .grid .center{text-align:center}
  .thai{font-family:"Sarabun","Open Sans",sans-serif}
  .lamp{display:inline-block;width:11px;height:11px;border-radius:50%;margin-left:4px;vertical-align:-1px}
  .lamp.red{background:radial-gradient(circle at 35% 35%,#ff6b6b,#d40000)}
  .lamp.amber{background:radial-gradient(circle at 35% 35%,#ffe27a,#f0b400)}
  .pager-row{position:absolute;left:0;width:100%;height:36px;border-top:1px solid var(--rule);border-bottom:1px solid var(--rule);display:flex;justify-content:center;align-items:center;gap:2px}
  .pager-row.flat{border-top:0}
  .pg-arrow{width:27px;height:26px;border-radius:4px;background:linear-gradient(180deg,#6b84a6,var(--pager-dark));display:flex;align-items:center;justify-content:center;margin:0 2px}
  .pg-num{width:22px;height:25px;border:1px solid #bdbdbd;border-radius:3px;background:linear-gradient(180deg,#f7f7f7,#dcdcdc);font-size:13.5px;color:#555;text-align:center;line-height:23px}
  .cta{position:absolute;left:533px;top:779px;width:452px;height:52px;border-radius:5px;border:1px solid #5c9a1e;
    background:linear-gradient(180deg,var(--green-top),var(--green-bot));color:#2c4a0f;font-size:17px;text-align:center;line-height:50px}
</style>
</head>
<body>
<div class="page">
  <header class="masthead">
    <svg class="masthead-bar" width="1011" height="40" viewBox="0 0 1011 40" aria-hidden="true">
      <path d="M0 40 V12 Q0 9 6 9 H305 L337 40 Z" fill="#ffffff"/>
      <path d="M305 9 L337 40 H1011 V0 H296 Z" fill="#000"/>
      <path d="M0 9 V0 H296 L305 9 Z" fill="var(--sky-deep)"/>
    </svg>
    <div class="system-name">Clearway Desk</div>
    <div class="brand"><span class="brand-dot"></span><span class="brand-name">NORVANE<br>PETROCHEMICAL</span></div>
    <nav class="nav">
      <a class="is-active" href="#"><svg width="150" height="40"><path d="M0 40 L22 4 Q24 0 30 0 H118 Q124 0 126 4 L150 40 Z" fill="var(--tab-active)"/></svg><span>Home</span></a>
      <a href="#"><svg width="128" height="40"><path d="M0 40 L20 4 Q22 0 28 0 H98 Q104 0 106 4 L128 40 Z" fill="var(--tab)" stroke="#fff"/></svg><span>Permits</span></a>
      <a href="#"><svg width="128" height="40"><path d="M0 40 L20 4 Q22 0 28 0 H98 Q104 0 106 4 L128 40 Z" fill="var(--tab)" stroke="#fff"/></svg><span>Report</span></a>
      <a href="#"><svg width="128" height="40"><path d="M0 40 L20 4 Q22 0 28 0 H98 Q104 0 106 4 L128 40 Z" fill="var(--tab)" stroke="#fff"/></svg><span>Admin</span></a>
      <a href="#"><svg width="128" height="40"><path d="M0 40 L20 4 Q22 0 28 0 H98 Q104 0 106 4 L128 40 Z" fill="var(--tab)" stroke="#fff"/></svg><span>Help</span></a>
    </nav>
    <div class="search"><span class="search-btn"><svg width="14" height="14" viewBox="0 0 14 14"><circle cx="6" cy="6" r="4.3" fill="none" stroke="#fff" stroke-width="1.8"/><path d="M9.2 9.2 L12.5 12.5" stroke="#fff" stroke-width="2" stroke-linecap="round"/></svg></span></div>
  </header>

  <section class="hero" role="img" aria-label="Petrochemical refinery plant lit up at dusk">
    <div class="hero-caption">Norvane Petrochemicals is simply dummy text of the printing and typesetting</div>
    <div class="hero-dots" style="top:auto;bottom:10px"><i class="on"></i><i></i><i></i></div>
  </section>
  <div class="body-shade"></div>

  <section class="panel" style="left:24px;top:360px;width:452px">
    <h2 class="panel-title"><em>New</em> Requests</h2>
    <table class="grid">
      <colgroup><col style="width:110px"><col style="width:149px"><col></colgroup>
      <tr><th>Request No.</th><th>Requested Date</th><th>Branch</th></tr>
      <tr><td><a href="#">56-0003</a></td><td>20/4/2013</td><td>GC1</td></tr>
      <tr><td><a href="#">56-0004</a></td><td>20/4/2013</td><td>GC2</td></tr>
    </table>
    <div class="pager-row" style="top:190px"><span class="pg-arrow"><svg width="8" height="10"><path d="M6 1 L2 5 L6 9" fill="none" stroke="#fff" stroke-width="2"/></svg></span><span class="pg-num">1</span><span class="pg-num">2</span><span class="pg-num">3</span><span class="pg-num">4</span><span class="pg-arrow"><svg width="8" height="10"><path d="M2 1 L6 5 L2 9" fill="none" stroke="#fff" stroke-width="2"/></svg></span></div>
  </section>

  <section class="panel" style="left:533px;top:360px;width:452px">
    <h2 class="panel-title"><em>My Working</em> Requests</h2>
    <table class="grid">
      <colgroup><col style="width:110px"><col style="width:119px"><col></colgroup>
      <tr><th>Request No.</th><th>Requested Date</th><th>Status</th></tr>
      <tr><td><a href="#">55-0200</a></td><td>20/4/2013</td><td>Waiting for process</td></tr>
      <tr><td><a href="#">55-0210</a></td><td>20/4/2013</td><td>In progress</td></tr>
      <tr><td><a href="#">55-0300</a></td><td>20/4/2013</td><td>Incomplete document</td></tr>
      <tr><td><a href="#">55-0301</a></td><td>20/4/2013</td><td>Cancel requested</td></tr>
    </table>
    <div class="pager-row flat" style="top:190px"><span class="pg-arrow"><svg width="8" height="10"><path d="M6 1 L2 5 L6 9" fill="none" stroke="#fff" stroke-width="2"/></svg></span><span class="pg-num">1</span><span class="pg-num">2</span><span class="pg-num">3</span><span class="pg-num">4</span><span class="pg-arrow"><svg width="8" height="10"><path d="M2 1 L6 5 L2 9" fill="none" stroke="#fff" stroke-width="2"/></svg></span></div>
  </section>

  <section class="panel" style="left:24px;top:597px;width:961px">
    <h2 class="panel-title"><em>Expiring</em> Permits</h2>
    <table class="grid">
      <colgroup><col style="width:119px"><col style="width:122px"><col style="width:254px"><col style="width:122px"><col style="width:157px"><col></colgroup>
      <tr><th>Permit No</th><th>Expire Date</th><th>Permit Name</th><th>Branch</th><th>Required Time (Day)</th><th>Required Time (Day)</th></tr>
      <tr><td><a href="#">AB56001</a></td><td>25/3/2013</td><td>Permit Name ###10</td><td>GC1</td><td class="num">30<span class="lamp red"></span></td><td class="center">-40</td></tr>
      <tr><td><a href="#">BIO5502</a></td><td>24/3/2013</td><td>Permit Name ###20</td><td>GC2</td><td class="num">60<span class="lamp amber"></span></td><td class="center">15</td></tr>
    </table>
    <div class="pager-row flat" style="top:129px;width:936px"><span class="pg-arrow"><svg width="8" height="10"><path d="M6 1 L2 5 L6 9" fill="none" stroke="#fff" stroke-width="2"/></svg></span><span class="pg-num">1</span><span class="pg-num">2</span><span class="pg-num">3</span><span class="pg-num">4</span><span class="pg-arrow"><svg width="8" height="10"><path d="M2 1 L6 5 L2 9" fill="none" stroke="#fff" stroke-width="2"/></svg></span></div>
  </section>

  <section class="panel" style="left:25px;top:775px;width:452px">
    <h2 class="panel-title"><em>My In Progress</em> Requests</h2>
    <table class="grid">
      <colgroup><col style="width:110px"><col style="width:149px"><col></colgroup>
      <tr><th>Request No.</th><th>Requested Date</th><th>Status</th></tr>
      <tr><td><a href="#">56-0003</a></td><td>20/4/2013</td><td class="thai">ระหว่างดำเนินการ</td></tr>
      <tr><td><a href="#">56-0004</a></td><td>20/4/2013</td><td class="thai">รอดำเนินการ</td></tr>
    </table>
    <div class="pager-row" style="top:237px"><span class="pg-arrow"><svg width="8" height="10"><path d="M6 1 L2 5 L6 9" fill="none" stroke="#fff" stroke-width="2"/></svg></span><span class="pg-num">1</span><span class="pg-num">2</span><span class="pg-num">3</span><span class="pg-num">4</span><span class="pg-arrow"><svg width="8" height="10"><path d="M2 1 L6 5 L2 9" fill="none" stroke="#fff" stroke-width="2"/></svg></span></div>
  </section>

  <a class="cta" href="#">New Request</a>

  <section class="panel" style="left:534px;top:843px;width:451px">
    <h2 class="panel-title"><em>Recent Completed</em> Requests</h2>
    <table class="grid">
      <colgroup><col style="width:139px"><col></colgroup>
      <tr><th>Request No.</th><th>Completed Date</th></tr>
      <tr><td><a href="#">55-0100</a></td><td>20/4/2013</td></tr>
      <tr><td><a href="#">55-0088</a></td><td>20/4/2013</td></tr>
      <tr><td><a href="#">55-0002</a></td><td>20/4/2013</td></tr>
    </table>
    <div class="pager-row flat" style="top:160px"><span class="pg-arrow"><svg width="8" height="10"><path d="M6 1 L2 5 L6 9" fill="none" stroke="#fff" stroke-width="2"/></svg></span><span class="pg-num">1</span><span class="pg-num">2</span><span class="pg-num">3</span><span class="pg-num">4</span><span class="pg-arrow"><svg width="8" height="10"><path d="M2 1 L6 5 L2 9" fill="none" stroke="#fff" stroke-width="2"/></svg></span></div>
  </section>
</div>
</body>
</html>
```